Business Card Design Project

After recently finishing a design project for the company logo using markbazaar, it's now time for a business card. Attached to this is the logo.

The requirements for the business card are pretty straightforward:

- A clean, uncomplicated look
- Consistent usage of fonts
- Designs for both single sided and double sided cards
- A modern layout with preferably space to refer to social media accounts and/or downloadable vcards through a qr code
- consistent application of the company colour scheme: red/white. Hex codes for exact colour can be provided

Thanks!

```html
<!DOCTYPE html>
<html lang="en">
<head>
<meta charset="utf-8">
<title>Kiln Row Recruiting – Business Card</title>
<link rel="stylesheet" href="https://fonts.googleapis.com/css2?family=Open+Sans:wght@400;600;700&display=swap">
<style>
  :root {
    --backdrop: #e9e5e0;
    --card-white: #ffffff;
    --ink: #231f20;
    --ink-soft: #333333;
    --band-dark: #2b2728;
    --band-light: #4a4546;
    --back-deep: #050505;
    --back-warm: #3a3534;
    --brand-red: #e31e26;
    --on-dark: #ffffff;
  }
  * { margin: 0; padding: 0; box-sizing: border-box; }
  html, body {
    width: 960px; height: 1200px; overflow: hidden;
    background: var(--backdrop);
    font-family: "Open Sans", Arial, sans-serif;
  }
  .card {
    position: absolute; left: 55px; width: 840px; height: 480px;
    border-radius: 28px; overflow: hidden;
  }
  .card--front { top: 88px; background: var(--card-white); }
  .card--back {
    top: 637px;
    background: linear-gradient(90deg, var(--back-deep) 0%, var(--back-warm) 28%, var(--back-warm) 100%);
  }

  /* front header band */
  .band-lead {
    position: absolute; left: 0; top: 86px; width: 93px; height: 55px;
    background: linear-gradient(90deg, var(--band-dark) 0%, var(--band-dark) 60%, var(--band-light) 100%);
  }
  .band-name {
    position: absolute; left: 348px; top: 86px; right: 0; height: 55px;
    background: linear-gradient(90deg, var(--band-dark) 0%, var(--band-dark) 70%, var(--band-light) 100%);
    color: var(--on-dark);
    display: flex; align-items: center; padding-left: 32px;
    font-size: 25px; white-space: nowrap;
  }
  .band-name .person { font-weight: 700; font-size: 29px; }
  .band-name .role { font-weight: 400; margin-left: 6px; }

  .wordmark { position: absolute; color: var(--ink); font-weight: 400; line-height: 1; white-space: nowrap; }
  .wordmark .name { display: block; }
  .wordmark .line { display: block; text-transform: uppercase; }

  .card--front .wordmark { left: 97px; top: 88px; }
  .card--front .wordmark .name { font-size: 52px; letter-spacing: -1px; }
  .card--front .wordmark .line { font-size: 27px; letter-spacing: 9px; margin-top: 2px; padding-left: 3px; }

  .contact-list { position: absolute; left: 100px; top: 255px; list-style: none; color: var(--ink-soft); font-size: 22px; }
  .contact-list li { display: flex; align-items: flex-start; line-height: 32px; }
  .contact-list li + li { margin-top: 10px; }
  .contact-list li.tight { margin-top: 2px; }
  .contact-list svg { width: 18px; height: 18px; margin: 7px 13px 0 0; flex: none; fill: var(--ink-soft); }

  /* back */
  .card--back .brand-square {
    position: absolute; left: 170px; top: 175px; width: 70px; height: 70px;
    background: var(--brand-red);
  }
  .card--back .wordmark { left: 263px; top: 155px; color: var(--on-dark); }
  .card--back .wordmark .name { font-size: 86px; letter-spacing: -2px; }
  .card--back .wordmark .line { font-size: 45px; letter-spacing: 13px; margin-top: 4px; }
</style>
</head>
<body>

<section class="card card--front" aria-label="Business card front">
  <div class="band-lead"></div>
  <div class="wordmark">
    <span class="name">Kiln Row</span>
    <span class="line">Recruiting</span>
  </div>
  <div class="band-name"><span class="person">Your Name -</span><span class="role">Designation</span></div>

  <ul class="contact-list">
    <li>
      <svg viewBox="0 0 20 20" aria-hidden="true"><path d="M2 8c0-3 4-4 8-4s8 1 8 4v1h-4V7.5c-1-.4-2.5-.6-4-.6s-3 .2-4 .6V9H2z"/><path d="M5 10l2-2h6l2 2v6H5z"/></svg>
      123-123-1234
    </li>
    <li>
      <svg viewBox="0 0 20 20" aria-hidden="true"><path d="M2 5h16v10H2zm1.5 1.3v.4L10 11l6.5-4.3v-.4zm0 2V13.7h13V8.3L10 12.6z" fill-rule="evenodd"/></svg>
      info@yourwebsite.com
    </li>
    <li class="tight">
      <svg viewBox="0 0 20 20" aria-hidden="true"><circle cx="10" cy="10" r="8"/><path d="M5 7c2 0 3 1 3 2s-2 1-2 3 2 2 2 4M12 4c0 2 2 2 3 3M13 12c1 0 2 1 2 3" stroke="#fff" stroke-width="1.3" fill="none"/></svg>
      www.kilnrow.com
    </li>
    <li>
      <svg viewBox="0 0 20 20" aria-hidden="true"><path d="M10 2l9 8h-3v8h-4v-5H8v5H4v-8H1z"/></svg>
      <span>1234, Street Name, City<br>District, Country Code.</span>
    </li>
  </ul>
</section>

<section class="card card--back" aria-label="Business card back">
  <div class="brand-square"></div>
  <div class="wordmark">
    <span class="name">Kiln Row</span>
    <span class="line">Recruiting</span>
  </div>
</section>

</body>
</html>
```